Larkwell Bus Card

i own a building in the bronx ny - its called "Larkwell House Co-op"i want a classy logo / business card - nothing too religuous but it is like a family there - its a large apartment building - colors i like dark red, black, medium shade of gray also reg business card stuff tel # 914-555-0173 address 4738 Larkwell Ave Bronx NY 10460 Email fijosh@aol.comslogan - " Neighbors under one roof "i can send u a picture of the building for the backside

```html
<!DOCTYPE html>
<html lang="en">
<head>
<meta charset="utf-8">
<title>Larkwell House Co-op – Business Card</title>
<link rel="stylesheet" href="https://fonts.googleapis.com/css2?family=Open+Sans:wght@400;600;700&family=Oswald:wght@500&display=swap">
<style>
  :root {
    --backdrop: #3a302c;
    --card-white: #f7f7f5;
    --card-black: #1f1f1f;
    --brand-red: #d3141b;
    --ink: #3c3c3c;
    --ink-soft: #555;
    --rule-light: #c9c9c9;
    --rule-dark: #4a4a4a;
    --white: #ffffff;
  }
  * { box-sizing: border-box; margin: 0; padding: 0; }
  html, body { width: 1200px; height: 844px; overflow: hidden; }
  body {
    background: var(--backdrop);
    font-family: "Open Sans", Arial, sans-serif;
    position: relative;
  }
  .card {
    position: absolute;
    top: 272px;
    width: 520px;
    height: 300px;
    border-radius: 3px;
    box-shadow: 0 10px 24px rgba(0,0,0,.45);
  }
  .card--front { left: 50px; background: var(--card-white); }
  .card--back  { left: 630px; background: var(--card-black); }

  .brand {
    display: flex;
    align-items: center;
    gap: 8px;
    font-family: "Open Sans", Arial, sans-serif;
    font-weight: 700;
    color: var(--brand-red);
    white-space: nowrap;
  }
  .brand__mark { background: var(--brand-red); flex: none; }

  .card--front .brand {
    position: absolute;
    right: 34px;
    top: 58px;
    font-size: 24px;
  }
  .card--front .brand__mark { width: 18px; height: 18px; }

  .rule { position: absolute; height: 1px; background: var(--rule-light); }
  .rule--top-1 { left: 250px; right: 34px; top: 104px; }
  .rule--top-2 { left: 130px; right: 34px; top: 126px; }

  .contact { position: absolute; left: 34px; right: 34px; bottom: 30px; }
  .contact__name {
    font-weight: 700; font-size: 17px; color: var(--brand-red);
    letter-spacing: .3px; line-height: 1.1;
  }
  .contact__title { font-size: 14px; color: var(--ink-soft); line-height: 1.3; }
  .contact__line { height: 1px; background: var(--rule-light); margin: 8px 0; }
  .contact__row { font-size: 14px; color: var(--ink); line-height: 1.4; }
  .contact__label { color: var(--brand-red); font-weight: 600; }
  .contact__sep { color: var(--ink-soft); margin: 0 8px; }

  .card--back .brand {
    position: absolute;
    left: 0; right: 0; top: 96px;
    justify-content: center;
    font-size: 30px;
  }
  .card--back .brand__mark { width: 22px; height: 22px; }
  .card--back .rule {
    background: var(--rule-dark);
    left: 110px; right: 110px;
  }
  .card--back .rule--upper { top: 148px; }
  .card--back .rule--lower { top: 206px; }
  .slogan {
    position: absolute;
    left: 0; right: 0; top: 160px;
    text-align: center;
    font-family: "Oswald", "Arial Narrow", sans-serif;
    font-weight: 500;
    font-size: 22px;
    color: var(--white);
  }
</style>
</head>
<body>
  <section class="card card--front" aria-label="Business card front">
    <div class="brand"><span class="brand__mark"></span>Larkwell House Co-op</div>
    <div class="rule rule--top-1"></div>
    <div class="rule rule--top-2"></div>
    <div class="contact">
      <p class="contact__name">DANIEL OKAFOR</p>
      <p class="contact__title">Managing Director</p>
      <div class="contact__line"></div>
      <p class="contact__row">4738 Larkwell Ave Bronx NY 10460</p>
      <div class="contact__line"></div>
      <p class="contact__row">
        <span class="contact__label">P:</span> 914-555-0173<span class="contact__sep">|</span><span class="contact__label">E:</span> mavreld@quintmail.com
      </p>
    </div>
  </section>

  <section class="card card--back" aria-label="Business card back">
    <div class="brand"><span class="brand__mark"></span>Larkwell House Co-op</div>
    <div class="rule rule--upper"></div>
    <p class="slogan">Neighbors under one roof</p>
    <div class="rule rule--lower"></div>
  </section>
</body>
</html>
```